Business Cards Design for the electrical wholesaler: clean bold dynamic :)

We need a business card design that would follow our latest brand guidelines. As an electrical wholesaler we want to bring a fresh look and feel into the industry. The design should be clean bold and dynamic. It should come alive with the renewed energy of our green colour. Our grey colour should keep things balanced and complement the notion of maturity and responsibility. We employ Lato as a corporate font however are not bound by this font and we’re open to interpretation here.

Target Market(s)

Electrical contractors

Industry/Entity Type

Business

Contact Information for Business Card

Logo
Name & Surname: Halyna Dorosh
Job Title: Director of Marketing
Email: halya.dorosh@quillmail.example
Cell phone: 780.555.0293
Address: 20517 - 87 Ave. Edmonton, AB, Canada. T6K 4N8
Business Phone: 780.555.0184
Website: www.brovix.example

Font styles to use
Other font styles liked:
• Lato

Requirements
Must have
• Logo & website
Nice to have
• Brand elements - some of them you may find in the attached Brand Guidelines (e.g. three lines on the background signifying "W")

```html
<!DOCTYPE html>
<html lang="en">
<head>
<meta charset="utf-8">
<title>Brovix Business Card</title>
<link href="https://fonts.googleapis.com/css2?family=Work+Sans:wght@400;500&display=swap" rel="stylesheet">
<style>
  :root {
    --green: #8dc63f;
    --grey: #4d4d4f;
    --white: #ffffff;
    --stage: #1c1c1c;
  }
  * { margin: 0; padding: 0; box-sizing: border-box; }
  html, body { width: 1200px; height: 897px; overflow: hidden; }
  body {
    background: var(--stage);
    font-family: "Work Sans", Arial, sans-serif;
    position: relative;
  }
  .card {
    position: absolute;
    left: 304px;
    width: 594px;
    height: 338px;
    border-radius: 18px;
    overflow: hidden;
  }
  .card-front { top: 92px; background: var(--white); }
  .card-back { top: 470px; background: var(--green); }
  .card-art { position: absolute; inset: 0; }

  .brand {
    position: absolute;
    display: flex;
    align-items: center;
    gap: 12px;
    font-weight: 400;
    letter-spacing: -1px;
    line-height: 1;
  }
  .brand-dot { border-radius: 50%; flex: none; }
  .card-front .brand { left: 28px; top: 34px; font-size: 60px; color: var(--grey); }
  .card-front .brand-dot { width: 44px; height: 44px; background: var(--green); }
  .card-back .brand { left: 50%; top: 128px; transform: translateX(-50%); font-size: 76px; color: var(--white); }
  .card-back .brand-dot { width: 54px; height: 54px; background: var(--white); }

  .person { position: absolute; right: 33px; top: 34px; text-align: right; }
  .person-name { font-size: 24px; font-weight: 500; color: var(--green); line-height: 1.2; }
  .person-title { font-size: 15.5px; color: var(--grey); letter-spacing: 0.5px; margin-top: 2px; }

  .contact {
    position: absolute;
    right: 33px;
    top: 184px;
    text-align: right;
    color: var(--white);
    font-size: 14px;
    letter-spacing: 0.3px;
    line-height: 19px;
  }
  .contact-line { display: flex; justify-content: flex-end; align-items: center; gap: 9px; }
  .contact-line svg { width: 11px; height: 11px; flex: none; }
  .address { margin-top: 9px; }

  .back-web {
    position: absolute;
    left: 0; right: 0;
    bottom: 25px;
    text-align: center;
    color: var(--white);
    font-size: 14px;
    letter-spacing: 0.6px;
  }
</style>
</head>
<body>

<section class="card card-front">
  <svg class="card-art" viewBox="0 0 594 338" aria-hidden="true">
    <path d="M0,252 C120,318 230,282 336,214 C430,156 510,140 594,164 L594,338 L0,338 Z" fill="var(--green)"/>
    <path d="M0,236 C70,282 180,272 294,192 C175,254 70,256 0,222 Z" fill="var(--grey)"/>
    <path d="M40,298 C170,312 262,252 362,196 C452,148 522,134 574,148" fill="none" stroke="var(--white)" stroke-width="3"/>
    <path d="M330,212 C430,150 520,132 574,148 C520,140 440,150 356,196 Z" fill="var(--green)"/>
  </svg>

  <div class="brand"><span class="brand-dot"></span>brovix</div>

  <div class="person">
    <div class="person-name">Halyna Dorosh</div>
    <div class="person-title">Director of Marketing</div>
  </div>

  <div class="contact">
    <div class="contact-line">780.555.0184
      <svg viewBox="0 0 12 12"><path d="M3,1 L5,3.5 L4,5 C4.8,6.6 5.6,7.4 7,8 L8.5,7 L11,9 L9.5,11 C5,10.5 1.5,7 1,2.5 Z" fill="none" stroke="var(--white)" stroke-width="1"/></svg>
    </div>
    <div class="contact-line">780.555.0293
      <svg viewBox="0 0 12 12"><rect x="3" y="0.5" width="6" height="11" rx="1" fill="none" stroke="var(--white)" stroke-width="1"/><circle cx="6" cy="9.5" r="0.7" fill="var(--white)"/></svg>
    </div>
    <div class="contact-line">halya.dorosh@quillmail.example
      <svg viewBox="0 0 12 12"><rect x="1" y="2.5" width="10" height="7" fill="none" stroke="var(--white)" stroke-width="1"/><path d="M1,2.5 L6,6.5 L11,2.5" fill="none" stroke="var(--white)" stroke-width="1"/></svg>
    </div>
    <div class="contact-line">www.brovix.example
      <svg viewBox="0 0 12 12"><circle cx="6" cy="6" r="5" fill="none" stroke="var(--white)" stroke-width="1"/><path d="M1,6 H11 M6,1 C3,4 3,8 6,11 M6,1 C9,4 9,8 6,11" fill="none" stroke="var(--white)" stroke-width="0.8"/></svg>
    </div>
    <div class="address">
      <div>20517 - 87 Ave. Edmonton, AB,</div>
      <div>Canada. T6K 4N8</div>
    </div>
  </div>
</section>

<section class="card card-back">
  <div class="brand"><span class="brand-dot"></span>brovix</div>
  <div class="back-web">www.brovix.example</div>
</section>

</body>
</html>
```